Commercial Real Estate

We need a business card design for a new commercial real estate business that specializes in apartment building brokerage. Not individual units but the entire complex. We find and represent the owners existing buildings and well as new buyers for those buildings. The design should convey trust, integrity, knowledge and growth. It should be easily read.

Target Market(s)

40 to 65 years old

Industry/Entity Type

Real Estate

```html
<!DOCTYPE html>
<html lang="en">
<head>
<meta charset="utf-8">
<title>Briarwood Business Card</title>
<link rel="stylesheet" href="https://fonts.googleapis.com/css2?family=PT+Sans:wght@400;700&display=swap">
<style>
  :root {
    --backdrop: #d3d4d6;
    --card-white: #ffffff;
    --band-grey: #ecebe6;
    --meadow: #869540;
    --slate: #4c5f5f;
    --teal: #6ec9ca;
    --teal-soft: #a9dcdc;
    --ink: #111111;
    --muted: #5b6b6b;
  }
  * { margin: 0; padding: 0; box-sizing: border-box; }
  html, body {
    width: 1200px;
    height: 1200px;
    overflow: hidden;
    background: var(--backdrop);
    font-family: "PT Sans", Arial, sans-serif;
  }
  .card {
    position: absolute;
    left: 150px;
    top: 343px;
    width: 902px;
    height: 513px;
    background: var(--card-white);
    overflow: hidden;
  }
  .card-backdrop { position: absolute; inset: 0; }
  .scene-art {
    position: absolute;
    left: 0;
    top: 31px;
    width: 318px;
    height: 410px;
    background: linear-gradient(180deg, var(--teal) 0%, #8cc3b2 55%, var(--meadow) 100%);
  }
  .brand {
    position: absolute;
    left: 518px;
    top: 24px;
    width: 332px;
    text-align: center;
    color: var(--slate);
  }
  .brand-name {
    font-size: 58px;
    font-weight: 700;
    letter-spacing: 2px;
    line-height: 1;
  }
  .brand-rule {
    height: 2px;
    margin-top: 8px;
    background: var(--teal);
  }
  .brand-tagline {
    margin-top: 6px;
    font-size: 18px;
    font-weight: 700;
    letter-spacing: 3.4px;
    white-space: nowrap;
  }
  .person {
    position: absolute;
    left: 596px;
    top: 225px;
  }
  .person-name {
    font-size: 31px;
    font-weight: 700;
    color: var(--ink);
    line-height: 1.1;
  }
  .person-title {
    font-size: 25px;
    color: var(--muted);
    line-height: 1.25;
  }
  .contact-list {
    position: absolute;
    right: 48px;
    top: 340px;
    list-style: none;
    text-align: right;
    color: var(--ink);
    font-size: 23px;
    line-height: 28px;
  }
  .contact-item {
    display: flex;
    justify-content: flex-end;
    align-items: flex-start;
    gap: 10px;
    margin-bottom: 5px;
  }
  .contact-item svg { flex: none; margin-top: 3px; }
  .contact-item.no-icon { padding-right: 34px; margin-top: -6px; }
  .website {
    position: absolute;
    left: 42px;
    top: 466px;
    display: flex;
    align-items: center;
    gap: 10px;
    color: var(--card-white);
    font-size: 24px;
  }
</style>
</head>
<body>
  <section class="card">
    <svg class="card-backdrop" viewBox="0 0 902 513" width="902" height="513" aria-hidden="true">
      <polygon points="0,0 468,0 0,239" fill="var(--band-grey)"/>
      <polygon points="902,137 902,260 520,383 438,383" fill="var(--band-grey)"/>
      <path d="M0,458 C70,420 130,383 198,383 L450,382 C620,380 780,340 902,293 L902,513 L0,513 Z" fill="var(--meadow)"/>
    </svg>

    <div class="scene-art" role="img" aria-label="Illustration of a tall curved glass apartment tower beside a broad leafy tree on a green lawn"></div>

    <header class="brand">
      <div class="brand-name">Briarwood</div>
      <div class="brand-rule"></div>
      <div class="brand-tagline">Property Investments</div>
    </header>

    <div class="person">
      <div class="person-name">Your Name</div>
      <div class="person-title">Your title</div>
    </div>

    <ul class="contact-list">
      <li class="contact-item">
        <span>555 555 5555</span>
        <svg width="24" height="24" viewBox="0 0 24 24" aria-hidden="true">
          <circle cx="12" cy="12" r="11" fill="var(--teal-soft)" stroke="#fff" stroke-width="1.5"/>
          <path d="M8 7 L10 7 L11 10 L9.5 11 Q11 14 13 14.5 L14 13 L17 14 L17 16 Q12 17 8 12 Q7 9 8 7 Z" fill="#fff"/>
        </svg>
      </li>
      <li class="contact-item">
        <span>555 555 5555</span>
        <svg width="24" height="24" viewBox="0 0 24 24" aria-hidden="true">
          <circle cx="12" cy="12" r="11" fill="var(--teal-soft)" stroke="#fff" stroke-width="1.5"/>
          <rect x="8.5" y="6" width="7" height="4" fill="#fff"/>
          <rect x="6.5" y="10" width="11" height="6" rx="1" fill="#fff"/>
          <rect x="8.5" y="14" width="7" height="3" fill="var(--teal-soft)" stroke="#fff"/>
        </svg>
      </li>
      <li class="contact-item">
        <span>Your company address</span>
        <svg width="24" height="24" viewBox="0 0 24 24" aria-hidden="true">
          <circle cx="12" cy="12" r="11" fill="var(--teal-soft)" stroke="#fff" stroke-width="1.5"/>
          <path d="M6 12 L12 6.5 L18 12 L16.5 12 L16.5 17 L7.5 17 L7.5 12 Z" fill="#fff"/>
        </svg>
      </li>
      <li class="contact-item no-icon"><span>City zipcode</span></li>
      <li class="contact-item">
        <span>your email address</span>
        <svg width="24" height="24" viewBox="0 0 24 24" aria-hidden="true">
          <circle cx="12" cy="12" r="11" fill="var(--teal-soft)" stroke="#fff" stroke-width="1.5"/>
          <rect x="6" y="8" width="12" height="8" fill="#fff"/>
          <path d="M6 8 L12 13 L18 8" fill="none" stroke="var(--teal-soft)" stroke-width="1.2"/>
        </svg>
      </li>
    </ul>

    <div class="website">
      <svg width="26" height="26" viewBox="0 0 24 24" aria-hidden="true">
        <circle cx="12" cy="12" r="11" fill="var(--teal-soft)" stroke="#fff" stroke-width="1.5"/>
        <circle cx="12" cy="12" r="6" fill="none" stroke="#fff" stroke-width="1.2"/>
        <ellipse cx="12" cy="12" rx="2.6" ry="6" fill="none" stroke="#fff" stroke-width="1"/>
        <line x1="6" y1="12" x2="18" y2="12" stroke="#fff" stroke-width="1"/>
      </svg>
      <span>www.yourdomain.com</span>
    </div>
  </section>
</body>
</html>
```